A-Stand Directional Sign Design

Objective:
We need a professional graphic design for an A-Stand sign that will guide customers arriving in our parking lot to our office. The design should be visually clear, welcoming, and aligned with our brand identity.
REQUIREMENTS:
Two versions of the design:
- One with an arrow pointing left
- One with an arrow pointing right
(This allows us to place the A-Stand anywhere and flip the graphic as needed.)
DIMENSIONS:
- Viewable Area: 30" x 40"
BRAND ALIGNMENT:
- Colors, fonts, and overall style should match our website: www.glidemarrow.com
- Clean, modern, and professional look consistent with our aviation/tourism brand
CONTENT:
- Clear directional arrow (left or right depending on version)
- Text: “Office Entrance” or similar concise wording (designers may propose alternatives if they improve clarity)
READABILITY:
- Bold, high-contrast design for visibility from a distance
- Simple layout that avoids clutter
DELIVERABLES:
- Final artwork in print-ready format (PDF preferred)
- Two versions: Arrow Left and Arrow Right
DESIGN GOAL:
Ensure customers can easily find our office upon arrival, while reinforcing glideMARROW’s professional and welcoming brand image.
Target Market(s)
Tourism
Look and feel

```html
<!DOCTYPE html>
<html lang="en">
<head>
<meta charset="utf-8">
<title>glideMARROW A-Stand Signs</title>
<link href="https://fonts.googleapis.com/css2?family=Bebas+Neue&display=swap" rel="stylesheet">
<style>
  :root {
    --stage: #2b2f37;
    --brand-blue: #2a7cc0;
    --brand-deep: #1f5f9e;
    --rim-blue: #86a6d4;
    --paper: #ffffff;
    --arrow-shade: #b9c9df;
  }
  html, body {
    margin: 0;
    padding: 0;
    width: 1200px;
    height: 2665px;
    overflow: hidden;
    background: var(--stage);
  }
  .stage {
    position: relative;
    width: 1200px;
    height: 2665px;
    display: flex;
    justify-content: center;
    align-items: center;
    gap: 40px;
  }
  .sign {
    position: relative;
    width: 540px;
    height: 720px;
    background: var(--brand-blue);
    box-shadow: 0 8px 22px rgba(0,0,0,0.45);
    overflow: hidden;
  }
  .sign-art {
    position: absolute;
    inset: 0;
    width: 540px;
    height: 720px;
  }
  .brand {
    position: absolute;
    left: 0;
    right: 0;
    top: 168px;
    display: flex;
    justify-content: center;
    align-items: center;
    gap: 14px;
  }
  .brand-dot {
    width: 30px;
    height: 30px;
    border-radius: 50%;
    background: var(--brand-deep);
  }
  .brand-name {
    font-family: "Bebas Neue", sans-serif;
    font-size: 66px;
    line-height: 1;
    letter-spacing: 2px;
    color: var(--brand-deep);
    text-transform: none;
  }
  .direction-label {
    position: absolute;
    left: 0;
    right: 0;
    top: 598px;
    text-align: center;
    font-family: "Bebas Neue", sans-serif;
    font-size: 86px;
    line-height: 1;
    color: var(--paper);
  }
</style>
</head>
<body>
<main class="stage">

  <section class="sign sign-left">
    <svg class="sign-art" viewBox="0 0 540 720" aria-hidden="false">
      <defs>
        <linearGradient id="arrowFillL" x1="0" y1="0" x2="0" y2="1">
          <stop offset="0" stop-color="#ffffff"/>
          <stop offset="0.55" stop-color="#f2f5fa"/>
          <stop offset="1" stop-color="#b9c9df"/>
        </linearGradient>
        <radialGradient id="photoGlowL" cx="0.5" cy="0.5" r="0.5">
          <stop offset="0" stop-color="#3f6f9f" stop-opacity="0.55"/>
          <stop offset="1" stop-color="#2a7cc0" stop-opacity="0"/>
        </radialGradient>
      </defs>
      <rect width="540" height="720" fill="#2a7cc0"/>
      <rect class="backdrop-photo" x="250" y="300" width="300" height="300" fill="url(#photoGlowL)" role="img" aria-label="Faded photo of a helicopter on the landing pad"/>
      <ellipse cx="292" cy="210" rx="335" ry="212" transform="rotate(-11 292 210)" fill="#86a6d4"/>
      <ellipse cx="272" cy="182" rx="330" ry="205" transform="rotate(-11 272 182)" fill="#ffffff"/>
      <g transform="translate(540 0) scale(-1 1)" fill="url(#arrowFillL)">
        <polygon points="32,440 98,440 150,497 98,554 32,554 84,497"/>
        <polygon points="138,440 204,440 256,497 204,554 138,554 190,497"/>
        <polygon points="244,440 402,440 402,412 512,497 402,582 402,554 244,554 296,497"/>
      </g>
    </svg>
    <div class="brand"><span class="brand-dot"></span><span class="brand-name">glideMARROW</span></div>
    <div class="direction-label">OFFICE ENTRANCE</div>
  </section>

  <section class="sign sign-right">
    <svg class="sign-art" viewBox="0 0 540 720" aria-hidden="false">
      <defs>
        <linearGradient id="arrowFillR" x1="0" y1="0" x2="0" y2="1">
          <stop offset="0" stop-color="#ffffff"/>
          <stop offset="0.55" stop-color="#f2f5fa"/>
          <stop offset="1" stop-color="#b9c9df"/>
        </linearGradient>
        <radialGradient id="photoGlowR" cx="0.5" cy="0.5" r="0.5">
          <stop offset="0" stop-color="#3f6f9f" stop-opacity="0.55"/>
          <stop offset="1" stop-color="#2a7cc0" stop-opacity="0"/>
        </radialGradient>
      </defs>
      <rect width="540" height="720" fill="#2a7cc0"/>
      <rect class="backdrop-photo" x="250" y="300" width="300" height="300" fill="url(#photoGlowR)" role="img" aria-label="Faded photo of a helicopter on the landing pad"/>
      <ellipse cx="292" cy="210" rx="335" ry="212" transform="rotate(-11 292 210)" fill="#86a6d4"/>
      <ellipse cx="272" cy="182" rx="330" ry="205" transform="rotate(-11 272 182)" fill="#ffffff"/>
      <g fill="url(#arrowFillR)">
        <polygon points="32,440 98,440 150,497 98,554 32,554 84,497"/>
        <polygon points="138,440 204,440 256,497 204,554 138,554 190,497"/>
        <polygon points="244,440 402,440 402,412 512,497 402,582 402,554 244,554 296,497"/>
      </g>
    </svg>
    <div class="brand"><span class="brand-dot"></span><span class="brand-name">glideMARROW</span></div>
    <div class="direction-label">OFFICE ENTRANCE</div>
  </section>

</main>
</body>
</html>
```